Day Spa Web Design Project

We just created a blog to add to our main site. We need the colors to match our main site and the look and feel of the blog to be smoother and less ameture looking, like the examples below.

Main Site, match this color scheme:
http://www.verelladayspa.com/

The project site:
http://blog.verelladayspa.com/

Our industry leaders blog site is our comparative and examples of what we need:
http://blog.wellnooklist.com/
http://blog.purelathermjournal.com/
http://thekelotabathblog.com/ (i like the layout a lot)
http://www.kneadharbor.com/blog/

Requirements
Must have
• social sharing.
Responsive design (already has it just keep it)
appealing mobile front page

```html
<!DOCTYPE html>
<html lang="en">
<head>
<meta charset="utf-8">
<title>Verella Day Spa Blog</title>
<link rel="stylesheet" href="https://fonts.googleapis.com/css2?family=Questrial&family=Arimo:wght@400;700&display=swap">
<style>
:root{
  --page:#fbecd6;
  --topbar:#e6bd82;
  --card:#fdf6ec;
  --card-rule:#dcb88c;
  --accent:#a4512e;
  --ink:#2b2420;
  --body:#3a3330;
  --footer:#ecd491;
  --footer-edge:#f3e1b6;
  --hero-white:#ffffff;
}
*{margin:0;padding:0;box-sizing:border-box}
html,body{width:900px;height:1200px;overflow:hidden}
body{position:relative;background:var(--page);font-family:"Arimo",Arial,sans-serif;color:var(--body)}
.top-bar{position:absolute;left:0;top:0;width:900px;height:35px;background:var(--topbar);font-family:"Questrial",sans-serif;font-size:9px;color:var(--ink)}
.top-nav{position:absolute;left:169px;top:13px;display:flex;gap:19px;letter-spacing:.2px}
.tagline{position:absolute;right:162px;top:13px}
.hero{position:absolute;left:149px;top:40px;width:599px;height:240px;border-radius:6px;
  background:linear-gradient(100deg,#d9b77e 0%,#7a5a2f 28%,#3d3a24 50%,#4e5a22 70%,#2b2a1c 100%)}
.hero-title{position:absolute;right:34px;top:26px;text-align:right;color:var(--hero-white);font-family:"Questrial",sans-serif}
.hero-title h1{font-size:32px;font-weight:400;line-height:1}
.hero-title p{font-size:12.5px;margin-top:4px}
.divider{position:absolute;left:384px;top:287px;width:152px;height:22px}
.card{position:absolute;width:189px;height:334px;background:var(--card);border-bottom:3px solid var(--card-rule);text-align:center}
.card-photo{position:absolute;left:7px;top:6px;width:173px;height:204px}
.card h2{position:absolute;left:0;right:0;top:215px;font-family:"Questrial",sans-serif;font-weight:400;font-size:12px;color:var(--accent);letter-spacing:.2px}
.card p{position:absolute;left:14px;right:14px;top:235px;font-size:7.2px;line-height:10.2px}
.card a{position:absolute;left:0;right:0;top:314px;font-size:7.2px;color:var(--accent);text-decoration:none}
.sidebar{position:absolute;left:597px;top:322px;width:160px;font-family:"Questrial",sans-serif}
.sidebar h3{font-weight:400;font-size:11.5px;color:var(--accent);margin-bottom:8px}
.sidebar ul{list-style:none;margin-left:11px;margin-bottom:20px}
.sidebar li{font-family:"Arimo",sans-serif;font-weight:700;font-size:6.8px;line-height:11px;color:var(--ink)}
.subscribe-note{font-family:"Arimo",sans-serif;font-weight:700;font-size:5.6px;line-height:11px;color:var(--ink);margin-top:-4px}
.subscribe-form{display:flex;align-items:center;margin-top:6px}
.subscribe-form input{width:120px;height:22px;border:1px solid var(--card-rule);background:#fff}
.subscribe-form span{margin-left:5px;font-size:8.5px;color:var(--accent)}
.footer{position:absolute;left:0;top:1048px;width:900px;height:152px;background:var(--footer)}
.footer-edge{position:absolute;left:0;top:1036px;width:900px;height:16px}
.footer-nav{position:absolute;left:167px;top:1077px;display:flex;gap:17px;font-family:"Questrial",sans-serif;font-size:8.5px;color:var(--accent)}
.copyright{position:absolute;left:166px;top:1090px;font-family:"Questrial",sans-serif;font-size:8.3px;color:var(--ink)}
.social{position:absolute;left:676px;top:1086px;display:flex;gap:5px}
.social span{width:12px;height:12px;border-radius:50%;background:#4b3a2c}
</style>
</head>
<body>
<header class="top-bar">
  <nav class="top-nav"><span>ABOUT US</span><span>CONTACT US</span></nav>
  <div class="tagline">Healthy Essentials for Good Living</div>
</header>

<section class="hero" role="img" aria-label="Spa still life with orchids, bamboo, rolled towel, stacked black stones and lit candles">
  <div class="hero-title">
    <h1>Verella Day Spa</h1>
    <p>Natural Treatments for Body, Skin &amp; Nails</p>
  </div>
</section>

<svg class="divider" viewBox="0 0 152 22" role="img" aria-label="Decorative scroll divider">
  <line x1="0" y1="11" x2="152" y2="11" stroke="#c9a987" stroke-width="1"/>
  <rect x="56" y="4" width="40" height="14" rx="7" fill="#d8bd9f"/>
</svg>

<article class="card" style="left:162px;top:324px">
  <div class="card-photo" role="img" aria-label="Woman relaxing on a massage table" style="background:linear-gradient(160deg,#e8c9cf,#f2dcd3 45%,#e9e6ee)"></div>
  <h2>KEYS TO STRESS REDUCTION</h2>
  <p>Some stress is natural, but often times stress becomes a problem when it leaves you feeling overwhelmed and out of control. Seventy seven percent of Americans report experiencing physical symptoms of stress, according to a 2012 study done by the National Wellness Research Council.</p>
  <a href="#">Read more..</a>
</article>

<article class="card" style="left:372px;top:324px">
  <div class="card-photo" role="img" aria-label="Runway models in bright spring dresses" style="background:linear-gradient(90deg,#f1d9c3 0%,#e6c79a 25%,#c9b47e 45%,#3f5660 65%,#d2a5bf 100%)"></div>
  <h2>WEARABLE SPRING TRENDS</h2>
  <p>Have you been paying attention to the latest spring fashion trends? If not, don't worry! We've got you covered from head to toe. This year, the runway trends are actually wearable for work or the weekend. From bold color combos to cool prints,</p>
  <a href="#">Read more..</a>
</article>

<article class="card" style="left:162px;top:685px">
  <div class="card-photo" role="img" aria-label="Woman receiving a hot stone treatment" style="background:linear-gradient(160deg,#e8a56d,#f1c9a4 50%,#2a2320 80%,#f4f1ec)"></div>
  <h2>SPA TIPS &amp; TRICKS</h2>
  <p>Some stress is natural, but often times stress becomes a problem when it leaves you feeling overwhelmed and out of control. Seventy seven percent of Americans report experiencing physical symptoms of stress, according to a 2012 study done by the National Wellness Research Council.</p>
  <a href="#">Read more..</a>
</article>

<article class="card" style="left:372px;top:685px">
  <div class="card-photo" role="img" aria-label="Orange flowers, white towel and a dish of smooth stones" style="background:linear-gradient(170deg,#e8782c,#f3b47a 35%,#f5f0ea 60%,#6c8fa2 85%,#b08a5a)"></div>
  <h2>SPA TIPS &amp; TRICKS</h2>
  <p>Some stress is natural, but often times stress becomes a problem when it leaves you feeling overwhelmed and out of control. Seventy seven percent of Americans report experiencing physical symptoms of stress, according to a 2012 study done by the National Wellness Research Council.</p>
  <a href="#">Read more..</a>
</article>

<aside class="sidebar">
  <h3>RECENT POSTS</h3>
  <ul><li>KEYS TO STRESS REDUCTION</li><li>WEARABLE SPRING TRENDS</li></ul>
  <h3>ARCHIVES</h3>
  <ul><li>APRIL 2013</li><li>MARCH 2013</li></ul>
  <h3>CATEGORIES</h3>
  <ul><li>MASSAGE</li><li>SPRING SEASON</li><li>SPA DEALS</li><li>TIPS &amp; TRICKS</li></ul>
  <h3>SUBSCRIBE</h3>
  <p class="subscribe-note">ENTER YOUR EMAIL ADDRESS TO FOLLOW THIS<br>BLOG AND RECEIVE NOTIFICATIONS DAILY</p>
  <div class="subscribe-form"><input type="text" aria-label="Email address"><span>GO</span></div>
</aside>

<svg class="footer-edge" viewBox="0 0 900 16" preserveAspectRatio="none" aria-hidden="true">
  <path d="M0 10 Q60 4 120 9 T240 8 T360 10 T480 6 T600 9 T720 7 T840 9 T900 8 V16 H0Z" fill="var(--footer-edge)"/>
</svg>
<footer class="footer"></footer>
<nav class="footer-nav"><span>HOME</span><span>CONTACT US</span></nav>
<div class="copyright">© COPYRIGHT 2013 VERELLA DAY SPA &nbsp;|&nbsp; 48 PALM GROVE AVE. SEABRIGHT, FL 33712</div>
<div class="social" aria-label="Social sharing"><span></span><span></span><span></span><span></span></div>
</body>
</html>
```